Healthcare and Professional IT Services Company need a redesigned business card

We are a IT Services company that targets small medical practices and professional business such as Attorneys, Accounts, Architects etc. We want to communicate a professional yet friendly image using recent logo redesign here on ArtHarbor. Like to see the colors blue and orange in the design. Must use the Tall Pine Computing as displayed in the new logo - then also want to incorporate the fish logo as well.

Target Market(s)

Small medical and professional services

Industry/Entity Type

It Company

Contact Information for Business Card

The usual stuff, place for name address phone website. Also maybe our tagline which is "rooted in technology"

Requirements
Must have
• My new logo and the fish somewhere on the card

```html
<!DOCTYPE html>
<html lang="en">
<head>
<meta charset="utf-8">
<title>Tall Pine Computing – Business Card</title>
<link href="https://fonts.googleapis.com/css2?family=Lato:wght@400;700&display=swap" rel="stylesheet">
<style>
  :root {
    --brand-blue: #27a8e0;
    --brand-blue-deep: #1d8fcc;
    --brand-orange: #f07f2c;
    --ink-white: #ffffff;
    --paper: #ffffff;
    --paper-shade: #ececec;
    --backdrop: #eef0f2;
    --card-shadow: rgba(0, 0, 0, 0.16);
  }
  * { box-sizing: border-box; margin: 0; padding: 0; }
  html, body {
    width: 1200px;
    height: 900px;
    overflow: hidden;
    background: var(--backdrop);
    font-family: "Lato", Arial, sans-serif;
  }
  .canvas { position: relative; width: 1200px; height: 900px; }

  .card {
    position: absolute;
    width: 560px;
    height: 320px;
    border-radius: 3px;
    overflow: hidden;
    box-shadow: 0 10px 26px var(--card-shadow);
  }

  /* ---------- Back of card ---------- */
  .card-back {
    left: 90px;
    top: 100px;
    background: var(--brand-blue);
  }
  .mascot-art {
    position: absolute;
    left: 175px;
    top: 60px;
    width: 210px;
    height: 125px;
    border-radius: 60px 70px 60px 50px;
    background: radial-gradient(ellipse at 65% 45%, #4bb8c9 0%, #2f86a8 55%, #e7793f 100%);
  }
  .tagline {
    position: absolute;
    left: 0;
    right: 0;
    top: 236px;
    text-align: center;
    color: var(--ink-white);
    font-weight: 700;
    font-size: 17px;
    letter-spacing: 0.2px;
  }

  /* ---------- Front of card ---------- */
  .card-front {
    left: 550px;
    top: 470px;
    background: var(--paper);
  }
  .brand-strip {
    position: absolute;
    left: 0; top: 0; right: 0;
    height: 168px;
    background: linear-gradient(180deg, var(--paper) 0%, var(--paper) 55%, var(--paper-shade) 100%);
  }
  .mascot-outline-art {
    position: absolute;
    left: 44px;
    top: 30px;
    width: 180px;
    height: 110px;
    border-radius: 50px 60px 50px 40px;
    background: linear-gradient(135deg, #d6eef9 0%, #a9dbf2 100%);
  }
  .brand-name {
    position: absolute;
    left: 246px;
    top: 62px;
    color: var(--brand-blue-deep);
    font-weight: 700;
    font-size: 30px;
    letter-spacing: -0.3px;
    white-space: nowrap;
  }
  .contact-band {
    position: absolute;
    left: 0; right: 0; bottom: 0;
    height: 152px;
    background: var(--brand-blue);
    color: var(--ink-white);
  }
  .person {
    position: absolute;
    right: 300px;
    top: 20px;
    text-align: right;
  }
  .person-name { font-size: 23px; font-weight: 700; line-height: 1.1; }
  .person-title { font-size: 16px; font-weight: 400; margin-top: 2px; }
  .person-address { font-size: 17px; line-height: 1.3; margin-top: 14px; }

  .contact-list {
    position: absolute;
    left: 296px;
    top: 12px;
    list-style: none;
  }
  .contact-list li {
    display: flex;
    align-items: center;
    height: 24px;
    font-size: 14.5px;
  }
  .contact-icon {
    width: 15px;
    height: 15px;
    margin-right: 8px;
    flex: none;
  }
</style>
</head>
<body>
<main class="canvas">

  <section class="card card-back" aria-label="Back of business card">
    <div class="mascot-art" role="img" aria-label="Cartoon fish mascot illustration in blue and orange"></div>
    <p class="tagline">"rooted in technology"</p>
  </section>

  <section class="card card-front" aria-label="Front of business card">
    <div class="brand-strip">
      <div class="mascot-outline-art" role="img" aria-label="Outline fish mascot illustration in blue"></div>
      <div class="brand-name">Tall Pine Computing</div>
    </div>

    <div class="contact-band">
      <div class="person">
        <p class="person-name">Dana Reyes</p>
        <p class="person-title">Managing Director</p>
        <p class="person-address">1234, Address GoesHere<br>Country, 12345</p>
      </div>

      <ul class="contact-list">
        <li>
          <svg class="contact-icon" viewBox="0 0 16 16" aria-hidden="true">
            <rect width="16" height="16" rx="2" fill="#fff"/>
            <path d="M4 3.5h2l1 2.5-1.3 1a6 6 0 0 0 3.3 3.3l1-1.3 2.5 1v2a1 1 0 0 1-1 1A9 9 0 0 1 3 4.5a1 1 0 0 1 1-1z" fill="var(--brand-blue)"/>
          </svg>
          123-456-7890
        </li>
        <li>
          <svg class="contact-icon" viewBox="0 0 16 16" aria-hidden="true">
            <rect width="16" height="16" rx="2" fill="#fff"/>
            <rect x="4" y="3" width="8" height="4" fill="var(--brand-blue)"/>
            <rect x="3" y="7" width="10" height="4" rx="1" fill="var(--brand-blue)"/>
            <rect x="5" y="10" width="6" height="3" fill="var(--brand-blue)"/>
          </svg>
          123-456-7890
        </li>
        <li>
          <svg class="contact-icon" viewBox="0 0 16 16" aria-hidden="true">
            <rect width="16" height="16" rx="2" fill="#fff"/>
            <rect x="3" y="4.5" width="10" height="7" fill="var(--brand-blue)"/>
            <path d="M3 4.5l5 4 5-4" fill="none" stroke="#fff" stroke-width="1"/>
          </svg>
          info@youremail.com
        </li>
        <li>
          <svg class="contact-icon" viewBox="0 0 16 16" aria-hidden="true">
            <rect width="16" height="16" rx="2" fill="#fff"/>
            <path d="M7 9l2-2M6.5 7.5l-1.5 1.5a1.8 1.8 0 0 0 2.5 2.5l1.5-1.5M9.5 8.5l1.5-1.5a1.8 1.8 0 0 0-2.5-2.5L7 6" fill="none" stroke="var(--brand-blue)" stroke-width="1.4" stroke-linecap="round"/>
          </svg>
          www.yourweb.com
        </li>
      </ul>
    </div>
  </section>

</main>
</body>
</html>
```